Animal Eye Clinic needs a Business card

We are a new veterinary ophthalmology practice (Ridgeline Pet Vision Care) and we need a business card designed. We only see animal eyes - we are not a regular veterinary clinic. We already have a logo. We are looking for a professional, good looking business card to hand out to our clients. We are looking for something simple but professional and contemporary. Our logo is likely the only picture/graphic that needs to be on the card.
Updates

Contact Information for Business Card

Delia Vossman, BSc, DVM, MSc, DipACVO
Veterinary Ophthalmologist

Phone: 250.418.3927
Email: ridgelinepetvisioncare@mailbox-example.net
Website: ridgelinepetvisioncare-example.net
Address: 1874 Thornbury Rd
Kelowna, BC, V1X 4M9

Colors

Designer to choose colors to be used in the design.

Requirements
Must have
• Our logo (attached)

```html
<!DOCTYPE html>
<html lang="en">
<head>
<meta charset="utf-8">
<title>Ridgeline Pet Vision Care — Business Card</title>
<link rel="stylesheet" href="https://fonts.googleapis.com/css2?family=Roboto:wght@300;400;700&display=swap">
<style>
  :root {
    --teal: #13a0ad;
    --teal-deep: #0e8f9b;
    --teal-soft: #e3f3f5;
    --ink: #5f6366;
    --grey-block: #8a8d8f;
    --rule: #7b7e80;
    --paper: #ffffff;
    --backdrop: #d9dcde;
  }
  * { margin: 0; padding: 0; box-sizing: border-box; }
  html, body { width: 1200px; height: 901px; overflow: hidden; }
  body {
    background: var(--backdrop);
    font-family: "Roboto", Arial, sans-serif;
    display: flex;
    flex-direction: column;
    align-items: center;
    justify-content: center;
    gap: 56px;
  }
  .card {
    width: 600px;
    height: 343px;
    position: relative;
    overflow: hidden;
    box-shadow: 0 10px 24px rgba(0,0,0,.22);
  }

  /* Back side */
  .card--back { background: var(--teal); }
  .back-pattern {
    position: absolute; inset: 0;
    background: linear-gradient(135deg, var(--teal) 0%, #1aa9b5 50%, var(--teal-deep) 100%);
  }
  .back-brand {
    position: absolute; right: 40px; top: 150px;
    display: flex; align-items: center; gap: 10px;
    color: var(--paper); font-weight: 700; font-size: 15px; letter-spacing: .5px;
  }
  .back-brand .dot { width: 14px; height: 14px; border-radius: 50%; background: var(--paper); }

  /* Front side */
  .card--front { background: var(--paper); }
  .front-emblem {
    position: absolute; right: 20px; top: -30px;
    width: 300px; height: 240px;
    border-radius: 50% 50% 50% 50% / 45% 45% 55% 55%;
    background: radial-gradient(circle at 60% 45%, #d3ecef 0%, var(--teal-soft) 55%, rgba(227,243,245,0) 75%);
  }
  .brand {
    position: absolute; left: 40px; top: 48px;
    display: flex; align-items: center; gap: 12px;
  }
  .brand .dot { width: 38px; height: 38px; border-radius: 50%; background: var(--teal); }
  .brand-name {
    color: var(--teal); font-weight: 700; font-size: 19px; line-height: 1.15;
    text-transform: uppercase; letter-spacing: .5px;
  }
  .person { position: absolute; left: 40px; top: 132px; }
  .person-name { color: var(--teal); font-weight: 700; font-size: 20px; }
  .person-name .creds { font-weight: 400; font-size: 12px; }
  .person-title { color: var(--ink); font-weight: 300; font-size: 16px; margin-top: 2px; }
  .contacts { position: absolute; left: 40px; top: 196px; list-style: none; }
  .contacts li {
    display: flex; align-items: center; gap: 8px;
    color: var(--ink); font-weight: 300; font-size: 14px; line-height: 21px;
  }
  .contacts svg { width: 12px; height: 12px; flex: none; }
  .contacts .accent { color: var(--teal); }
  .rule { position: absolute; left: 40px; right: 40px; top: 272px; height: 1px; background: var(--rule); }
  .address {
    position: absolute; left: 40px; top: 280px;
    color: var(--ink); font-weight: 300; font-size: 14px;
  }
  .band { position: absolute; left: 0; right: 0; bottom: 0; height: 14px; display: flex; }
  .band .grey { width: 44px; background: var(--grey-block); }
  .band .color { flex: 1; background: var(--teal); margin-left: 6px; }
</style>
</head>
<body>

  <section class="card card--back" aria-label="Card back">
    <div class="back-pattern" role="img" aria-label="Repeating pattern of the clinic emblem in lighter teal"></div>
    <div class="back-brand"><span class="dot"></span>Ridgeline Pet Vision Care</div>
  </section>

  <section class="card card--front" aria-label="Card front">
    <div class="front-emblem" role="img" aria-label="Large faint clinic emblem decoration"></div>

    <div class="brand">
      <span class="dot"></span>
      <div class="brand-name">Ridgeline<br>Pet Vision Care</div>
    </div>

    <div class="person">
      <div class="person-name">Delia Vossman<span class="creds">, BSc, DVM, MSc, DipACVO</span></div>
      <div class="person-title">Veterinary Ophthalmologist</div>
    </div>

    <ul class="contacts">
      <li>
        <svg viewBox="0 0 12 12" aria-hidden="true"><path fill="#13a0ad" d="M2.5 1 4.3 1 5 3.6 3.9 4.5a6.5 6.5 0 0 0 3.6 3.6L8.4 7 11 7.7V9.5C11 10.3 10.3 11 9.5 11 4.8 11 1 7.2 1 2.5 1 1.7 1.7 1 2.5 1Z"/></svg>
        250.418.3927
      </li>
      <li>
        <svg viewBox="0 0 12 12" aria-hidden="true"><rect x="1" y="2.5" width="10" height="7" fill="#13a0ad"/><path d="M1 2.5 6 6.5 11 2.5" fill="none" stroke="#fff" stroke-width="1"/></svg>
        ridgelinepetvisioncare@mailbox-example.net
      </li>
      <li>
        <svg viewBox="0 0 12 12" aria-hidden="true"><circle cx="6" cy="6" r="5" fill="#13a0ad"/><path d="M1 6h10M6 1c2 2.5 2 7.5 0 10M6 1c-2 2.5-2 7.5 0 10" fill="none" stroke="#fff" stroke-width=".8"/></svg>
        <span>www.<span class="accent">ridgelinepetvisioncare-example</span>.net</span>
      </li>
    </ul>

    <div class="rule"></div>
    <div class="address">1874 Thornbury Rd, Kelowna, BC, V1X 4M9</div>

    <div class="band"><span class="grey"></span><span class="color"></span></div>
  </section>

</body>
</html>
```